Website Redesign - We Need Your Magic!

Hello we are looking for you to help us re-design a high end and professional website for a high-end private school.

Here is the current site: http://www.ferndalecrest.com/

NOTE THIS IS DESIGN ONLY, NO CODING :)

The image they want to portray is that of high quality sports and education, in a creative "un-stiff" way.

Menu Bar: Horizontal

Look and Feel:

Site Colors: Dark green and a Gold yellow (logos are attached)

This site will represent a school so the look must be clean, bold, and classy. The site must have a very clean user interface, with things easily recognizable. Think simple.

The site should be visually appealing! If you come to me with templates, or a ton of text you will be out.

This site should be outside the box, we do not want boring, we do not want status quo. This site should instill excitement, innovation, and athletics.

So the main points again are:

1. High-end and classy look, with creative feel
2. Simple and clear navigation style
3. To cover the Junior and High School - Ferndale Crest College Schools

Think outside the box. We look forward to seeing what you come up with!!

Thank you for helping us create an amazing site for the school!

Industry/Entity Type

School

```html
<!DOCTYPE html>
<html lang="en">
<head>
<meta charset="utf-8">
<title>Ferndale Crest College</title>
<link href="https://fonts.googleapis.com/css2?family=Arimo:wght@400;700&family=PT+Sans:wght@700&display=swap" rel="stylesheet">
<style>
:root{
  --green:#0e4a1e;
  --green-dark:#0b3a17;
  --gold:#d7c400;
  --gold-btn:#d4b400;
  --ink:#222;
  --muted:#555;
  --page:#f2f2f2;
  --foot:#222;
  --foot-bar:#161616;
  --line:#ddd;
}
*{margin:0;padding:0;box-sizing:border-box}
html,body{width:800px;height:1200px;overflow:hidden}
body{background:var(--page);font-family:"Arimo",Arial,sans-serif;color:var(--ink);position:relative}
.abs{position:absolute}
.crest{left:86px;top:18px;width:82px;height:82px;border-radius:50%;background:var(--green);border:4px solid var(--gold)}
.site-title{left:182px;top:52px;font-size:26px;font-weight:700;color:var(--green);letter-spacing:.5px}
.contact{left:575px;top:45px;font-size:11px;line-height:18px}
.contact div{display:flex;align-items:center;gap:10px}
.contact a{color:var(--ink)}
.search{left:572px;top:94px;width:145px;height:24px;display:flex}
.search span{flex:1;background:#eee;border:1px solid #ccc;font-size:8px;color:#999;padding:7px 7px}
.search b{width:33px;background:#111;color:#fff;font-size:12px;text-align:center;line-height:24px}
.nav{left:0;top:130px;width:800px;height:33px;background:var(--green);display:flex;align-items:center;padding-left:76px}
.nav a{color:#fff;font-size:9.5px;text-decoration:none;padding:0 16px;border-right:1px solid #2c6a3a;height:21px;line-height:21px}
.nav a:last-child{border:none}
.nav a.active{background:var(--gold);color:var(--green);padding:0 16px;margin-right:16px;border:none}
.hero{left:73px;top:163px;width:652px;height:263px;background:linear-gradient(180deg,#cfd8d0 0%,#9bb07a 55%,#5f7a3a 100%)}
.arrow{width:26px;height:25px;background:#111;top:276px}
.caption{left:467px;top:356px;width:240px;height:58px;background:rgba(20,20,20,.85);text-align:center;font-family:"PT Sans",sans-serif;padding-top:6px}
.caption p{font-size:19px;color:#fff}
.caption p+p{font-size:15px;color:var(--gold);margin-top:2px}
.main{left:75px;top:440px;width:400px}
h1,h2,h3{font-weight:700;letter-spacing:.5px}
.main h1{font-size:18.5px;margin-bottom:14px;color:#222}
.main h2{font-size:15px;margin:28px 0 20px}
.main p{font-size:8.8px;line-height:13.5px;margin:0 2px 13px}
.main strong.g{color:var(--green)}
.head{display:flex;gap:13px}
.portrait{width:96px;height:83px;flex:none;border:3px solid #ddd;background:linear-gradient(135deg,#1d5a35,#2f6e45 60%,#8a7a60)}
.signup{left:526px;top:446px;width:199px;height:174px;background:var(--green);border-radius:3px;padding:9px 10px;color:#fff}
.signup h3{font-size:17px;margin-bottom:6px}
.signup p{font-size:8.5px;line-height:12px;color:#dfe;margin-bottom:9px}
.field{background:#fff;height:22px;font-size:7.5px;color:#888;padding:7px 6px;margin-bottom:12px;width:167px}
.btn{width:97px;height:23px;background:var(--gold-btn);border-radius:2px;color:var(--green-dark);font-size:12px;font-weight:700;text-align:center;line-height:23px}
.side{left:524px;width:201px}
.side h3{font-size:15px;color:#333;padding-bottom:8px;margin-bottom:14px;border-bottom:3px solid var(--green);position:relative}
.side h3::after{content:"";position:absolute;left:0;bottom:-3px;width:32px;height:3px;background:var(--gold)}
.side li{list-style:none;font-size:8.5px;padding:0 0 8px 16px;margin-left:4px;position:relative;border-bottom:1px dotted var(--line);margin-bottom:8px}
.side li::before{content:"";position:absolute;left:2px;top:2px;border-left:4px solid #333;border-top:3px solid transparent;border-bottom:3px solid transparent}
.side .small li{font-size:7.5px;padding-bottom:9px;margin-bottom:7px}
.more{text-align:right;font-size:8.5px;color:var(--green);padding-right:10px}
.like{left:526px;top:920px;width:159px;height:51px;background:#2a5ea8;color:#fff;font-size:14px;font-weight:700;text-align:center;line-height:51px}
.count{left:692px;top:923px;width:32px;height:46px;font-size:8px;text-align:center}
.count span{display:block;border:1px solid #ccc;background:#fff;height:22px;line-height:22px;margin-bottom:3px}
.count b{display:block;background:#3b5998;color:#fff;height:14px;line-height:14px}
.footer{left:0;top:1032px;width:800px;height:140px;background:var(--foot)}
.foot-bar{left:0;top:1172px;width:800px;height:28px;background:var(--foot-bar);color:#ccc;font-size:8px;text-align:center;line-height:28px}
.addr{left:120px;top:1067px;color:#fff;text-align:right;font-size:8px;line-height:12px}
.addr h4{font-size:12.5px;letter-spacing:.5px;margin-bottom:3px}
.addr a{color:#ddd;display:block;margin-top:7px}
.divider{top:1057px;width:0;height:92px;border-left:1px dotted #555}
.follow{left:300px;top:1065px;width:160px;text-align:center;color:#fff;font-size:12px;font-weight:700;letter-spacing:.5px}
.social{display:flex;justify-content:center;gap:10px;margin-top:28px}
.social span{width:26px;height:26px;border-radius:50%;background:#2a5ea8;border:2px solid #ccc}
.social em{font-style:normal;font-size:7px;font-weight:400;color:#bbb;display:block;margin-top:4px}
.badge{background:#4a4a4a;border-radius:3px}
</style>
</head>
<body>
<div class="abs crest" aria-hidden="true"></div>
<div class="abs site-title">Ferndale Crest College</div>

<div class="abs contact">
  <div><svg width="12" height="12" viewBox="0 0 24 24"><path fill="#111" d="M6.6 10.8a15 15 0 0 0 6.6 6.6l2.2-2.2a1 1 0 0 1 1-.25 11.4 11.4 0 0 0 3.6.57 1 1 0 0 1 1 1V20a1 1 0 0 1-1 1A17 17 0 0 1 3 4a1 1 0 0 1 1-1h3.5a1 1 0 0 1 1 1c0 1.25.2 2.45.57 3.57a1 1 0 0 1-.25 1z"/></svg><span>0741 208 316 / 0741 559 072</span></div>
  <div><svg width="13" height="9" viewBox="0 0 26 18"><rect x="1" y="1" width="24" height="16" fill="none" stroke="#111" stroke-width="2"/><path d="M1 1l12 9 12-9" fill="none" stroke="#111" stroke-width="2"/></svg><a href="#">admin@ferndalecrest.com</a></div>
</div>
<div class="abs search"><span>Search....</span><b>GO</b></div>

<nav class="abs nav">
  <a class="active" href="#">HOME</a>
  <a href="#">ABOUT US</a>
  <a href="#">ACADEMICS</a>
  <a href="#">SPORTS</a>
  <a href="#">JOINING FERNDALE</a>
  <a href="#">ABOUT US</a>
  <a href="#">CONTACT US</a>
</nav>

<div class="abs hero" role="img" aria-label="Photo of young pupils playing football on a grass pitch"></div>
<div class="abs arrow" style="left:72px"><svg width="26" height="25"><path d="M16 5l-7 7.5 7 7.5" fill="none" stroke="#fff" stroke-width="2"/></svg></div>
<div class="abs arrow" style="left:700px"><svg width="26" height="25"><path d="M10 5l7 7.5-7 7.5" fill="none" stroke="#fff" stroke-width="2"/></svg></div>
<div class="abs caption"><p>Stepping Ahead in</p><p>Education, Culture, Sport &amp; Life</p></div>

<main class="abs main">
  <h1>Welcome to Ferndale Crest College</h1>
  <p>Welcome to <strong class="g">Ferndale Crest Group of Schools</strong> where our School Motto is ‘Unitas’ meaning Togetherness. We aim to work together in every aspect of School life, from academics to sport.</p>
  <p>Ferndale Crest College opened on 14th February 1983 and occupies 120 ha of land amidst the low hills of the Corran Range, 8km west of Ashbury. This location encourages focus on School life away from the distractions and hustle and bustle of the larger towns.</p>
  <p>The day scholars have the option of selected bus drop off points for parents to collect day scholars closer to home.</p>
  <p>Ferndale Crest College offers a wide range of academic subjects alongside a varied sport and extra-curricular program.</p>
  <h2>Headmaster's Message</h2>
  <div class="head">
    <div class="portrait" role="img" aria-label="Portrait photo of the headmaster"></div>
    <div>
      <p><strong>Welcome to Ferndale Crest College. Here at the College we aim to encourage each pupil to be a self-confident, well-rounded individual.</strong></p>
      <p>We aim to propel them to the highest level of achievement in both academics and extra-curricular activities to provide them with the life skills they will need when they leave the College and to prepare them to be of value to society.</p>
    </div>
  </div>
  <p>The College is a warm community which lives out high standards and is rightly proud of its achievements.</p>
  <p>We are a small enough School for each pupil to be known well, but large enough to offer a wide range of subjects and experience.Our Website covers many aspects of the College from how to apply for a place, to the curriculum and to much more. I hope you find it helpful and interesting.</p>
  <p>Please visit and meet the pupils, the staff and see for yourself what Ferndale Crest College can offer your son or daughter.</p>
  <p><strong>I look forward to welcoming you and your family to Ferndale Crest College.</strong></p>
</main>

<aside class="abs signup">
  <h3>Email Sign Up</h3>
  <p>If you would like to be added to the list of parents that receive the School Newsletter,</p>
  <div class="field">Enter Your name</div>
  <div class="field">Enter Your email</div>
  <div class="btn">SUBSCRIBE</div>
</aside>

<section class="abs side" style="top:647px">
  <h3>Upcoming Events</h3>
  <ul>
    <li>Robotic competitions teach students</li>
    <li style="border:none;margin-bottom:0">Robotic competitions teach students how to</li>
  </ul>
  <div class="more">More Events...</div>
</section>

<section class="abs side small" style="top:757px">
  <h3>Important Links</h3>
  <ul>
    <li>School Calender</li>
    <li>Registration Form</li>
    <li>Sports Announcements</li>
    <li style="border:none">2nd Term 2014 Termly Calendar</li>
  </ul>
</section>

<div class="abs like">Like us on Friendbook</div>
<div class="abs count"><span>60k</span><b>Like</b></div>

<footer class="abs footer"></footer>
<svg class="abs" style="left:74px;top:1066px" width="31" height="42" viewBox="0 0 30 40"><path d="M15 0a15 15 0 0 0-15 15c0 11 15 25 15 25s15-14 15-25A15 15 0 0 0 15 0z" fill="#9a9a9a"/><circle cx="15" cy="15" r="5" fill="#222"/></svg>
<div class="abs addr">
  <h4>Ferndale Crest College</h4>
  <div>12 Harlow Street,</div>
  <div>Eastmere Vic 3090</div>
  <a href="#">Click here to see the directions &gt;&gt;</a>
</div>
<div class="abs divider" style="left:293px"></div>
<div class="abs follow">Follow Us On:
  <div class="social"><div><span style="display:block"></span><em>Friendbook</em></div><div><span style="display:block;background:#2a8fd6"></span><em>Chirper</em></div></div>
</div>
<div class="abs divider" style="left:470px"></div>
<div class="abs badge" style="left:505px;top:1062px;width:68px;height:30px"></div>
<div class="abs badge" style="left:590px;top:1062px;width:70px;height:30px"></div>
<div class="abs badge" style="left:497px;top:1106px;width:82px;height:30px"></div>
<div class="abs badge" style="left:590px;top:1106px;width:72px;height:30px"></div>
<div class="abs" style="left:682px;top:1076px;width:44px;height:44px;border-radius:50%;background:#d8d8d8"></div>

<div class="abs foot-bar">Copyright © 2015 Ferndale Crest. All Rights Reserved.</div>
</body>
</html>
```